Emergency Management Consulting Needs a Website

Need to develop a website for an Emergency Management Consulting business. This website needs to be user friendly and resemble disaster preparedness, response, recovery, and mitigation. It must allow for me to make changes to it myself by adding pages, content and pictures. Looking for an advanced page to the website that allows monitoring of social media sites, hashtags, and keywords. Must have pictures of disasters on the site. Must try to integrate the logo colors, not excessive.

Reason: Did not receive anything sufficient to what I am looking for.

Industry/Entity Type

Government

Coding

Coded - Design and coding required

Number of Pages Required

5+ page

Requirements
Must have
• Logo, advanced social media monitoring page, allow for edits myself (content, pages, graphics) this must be a CMS of some sort, use logo color scheme (not excessively), must be professional looking, connect with Plivex Domain, find a hosting site, SEO, no "long" designs, minimize "dead" space, no social media feeds, no newsletter stuff.
• Menu items: Home, About Us, Services, Situation Monitor, Work With Us, Contact Us (hopefully these could be editable if I need to later)
• When you make a submission, please send me a message on which CMS you are using. Thank you.
Nice to have
• Examples of websites:
• https://www.qrt.vic.gov.au/
• http://www.larkenmoss.example/
• http://www.tulpaxo.example/
• http://vonmirelconsulting.example/
• http://www.calvornet.example/services/emergency-management
• https://zuq.example/
• http://www.vestimora.example/Responsibility/Sustainable-Development/HSE/Crisis-and-Emergency-Management/

```html
<!DOCTYPE html>
<html lang="en">
<head>
<meta charset="utf-8">
<title>What People Say · Our Team</title>
<link href="https://fonts.googleapis.com/css2?family=Montserrat:wght@400;600;700;800&display=swap" rel="stylesheet">
<style>
  :root {
    --brand-red: #dc2226;
    --band-red: #d41d1f;
    --band-red-light: #e0302e;
    --band-red-deep: #c8181b;
    --ink: #0d0d0d;
    --muted: #8a8a8a;
    --white: #ffffff;
  }
  * { box-sizing: border-box; margin: 0; padding: 0; }
  html, body { width: 1200px; height: 865px; overflow: hidden; background: var(--white); }
  body { font-family: "Montserrat", Arial, sans-serif; position: relative; }

  .testimonials { position: absolute; left: 0; top: 0; width: 1200px; height: 434px; }
  .testimonials__backdrop {
    position: absolute; inset: 0;
    background: linear-gradient(160deg, var(--band-red-light), var(--band-red) 45%, var(--band-red-deep) 70%, var(--band-red-light));
  }
  .section-title {
    position: absolute; left: 0; width: 100%; text-align: center;
    font-weight: 800; font-size: 32px; letter-spacing: 0.6px; line-height: 40px;
  }
  .testimonials .section-title { top: 44px; color: var(--white); }

  .quote-card {
    position: absolute; left: 158px; top: 127px; width: 884px; height: 181px;
    background: var(--white); border-radius: 16px;
  }
  .quote-card__pointer { position: absolute; left: 446px; top: 180px; }
  .quote-card__mark { position: absolute; left: 29px; top: 29px; }
  .quote-card__text {
    position: absolute; left: 79px; top: 35px; width: 766px;
    font-size: 12px; line-height: 14.4px; color: var(--muted); letter-spacing: 0.55px;
  }
  .quote-card__author {
    position: absolute; left: 0; top: 118px; width: 100%; text-align: center;
    font-size: 19px; line-height: 24px; font-weight: 700; color: var(--ink); letter-spacing: 0.6px;
  }
  .quote-card__author .name { color: var(--brand-red); }

  .avatar-strip { position: absolute; top: 345px; left: 0; width: 100%; height: 51px; }
  .avatar {
    position: absolute; width: 51px; height: 51px; border-radius: 50%;
    border: 3px solid var(--white);
    background: radial-gradient(circle at 50% 45%, #c99a7e, #4a3128);
    box-shadow: 0 2px 4px rgba(0,0,0,.25);
  }

  .team .section-title { top: 497px; color: var(--ink); }
  .team .section-title .accent { color: var(--brand-red); }

  .member { position: absolute; top: 576px; width: 200px; text-align: center; }
  .member__portrait {
    width: 165px; height: 165px; margin: 0 auto; border-radius: 50%;
    background: var(--white); box-shadow: 0 0 6px rgba(0,0,0,.12); padding: 8px;
  }
  .member__photo { width: 149px; height: 149px; border-radius: 50%; }
  .member__photo--mono { background: radial-gradient(circle at 50% 45%, #d8d8d8, #3a3a3a); }
  .member__photo--stone { background: radial-gradient(circle at 50% 45%, #c9a58d, #5d5a55); }
  .member__photo--warm { background: radial-gradient(circle at 50% 50%, #d29a7e, #3a2016 75%); }
  .member__photo--light { background: radial-gradient(circle at 50% 45%, #caa692, #e6e3de 70%); }
  .member__name {
    margin-top: 14px; font-size: 21px; font-weight: 700; color: var(--brand-red);
    letter-spacing: 0.6px; line-height: 24px;
  }
  .member__role { font-size: 16px; font-weight: 700; color: var(--ink); letter-spacing: 0.9px; line-height: 18px; }
</style>
</head>
<body>
  <section class="testimonials">
    <div class="testimonials__backdrop" role="img" aria-label="Red-tinted mosaic of disaster response and recovery photographs"></div>
    <h2 class="section-title">WHAT PEOPLE SAY</h2>

    <div class="quote-card">
      <svg class="quote-card__mark" width="46" height="34" viewBox="0 0 38 30" aria-hidden="true">
        <path fill="var(--brand-red)" d="M8 0h9L10 14c5 0 7 4 7 8 0 5-4 8-8 8-5 0-9-3-9-9 0-5 3-12 8-21zM28 0h9L30 14c5 0 7 4 7 8 0 5-4 8-8 8-5 0-9-3-9-9 0-5 3-12 8-21z"/>
      </svg>
      <p class="quote-card__text">When the floods reached our district, their team had already helped us build a clear preparedness plan, train our volunteers and map every shelter. During the response they kept our coordinators informed hour by hour, and through recovery they guided us on mitigation work so that the next storm season finds our community ready, calm and far better protected than before.</p>
      <p class="quote-card__author"><span class="name">John Doe</span> | NGO</p>
      <svg class="quote-card__pointer" width="22" height="13" viewBox="0 0 22 13" aria-hidden="true">
        <path fill="var(--white)" d="M0 0h22L11 13z"/>
      </svg>
    </div>

    <div class="avatar-strip">
      <div class="avatar" style="left:446px" role="img" aria-label="Testimonial author portrait"></div>
      <div class="avatar" style="left:511px" role="img" aria-label="Testimonial author portrait"></div>
      <div class="avatar" style="left:575px" role="img" aria-label="Testimonial author portrait"></div>
      <div class="avatar" style="left:639px" role="img" aria-label="Testimonial author portrait"></div>
      <div class="avatar" style="left:703px" role="img" aria-label="Testimonial author portrait"></div>
    </div>
  </section>

  <section class="team">
    <h2 class="section-title">OUR <span class="accent">TEAM</span></h2>

    <div class="member" style="left:119px">
      <div class="member__portrait"><div class="member__photo member__photo--mono" role="img" aria-label="Emergency management team member portrait"></div></div>
      <p class="member__name">JOHN DOE</p>
      <p class="member__role">Member</p>
    </div>
    <div class="member" style="left:373px">
      <div class="member__portrait"><div class="member__photo member__photo--stone" role="img" aria-label="Emergency management team member portrait"></div></div>
      <p class="member__name">JOHN DOE</p>
      <p class="member__role">Member</p>
    </div>
    <div class="member" style="left:630px">
      <div class="member__portrait"><div class="member__photo member__photo--warm" role="img" aria-label="Emergency management team member portrait"></div></div>
      <p class="member__name">JOHN DOE</p>
      <p class="member__role">Member</p>
    </div>
    <div class="member" style="left:886px">
      <div class="member__portrait"><div class="member__photo member__photo--light" role="img" aria-label="Emergency management team member portrait"></div></div>
      <p class="member__name">JOHN DOE</p>
      <p class="member__role">Member</p>
    </div>
  </section>
</body>
</html>
```